Künstlerisches CD-Cover für Album
Zielgruppe
Ich bin ein Künstler im musikalischen Bereich. Meine Musikrichtung ist kombiniert aus den Bereichen des Rapps und dem Gesang. Mein Stil ist eher Gefühlvoll. Passend dazu suche ich ein echt künstleriches CD-Cover für mein Album >>> Spur im Nebel <<< .
Aufgabenstellung
Ich lege besonderen Wert auf echt kreative und künstlerische Fähigkeiten bei der Umsetzug des CD-Covers. Dieses Cover sollte ein echter Blickfang werden und zu meinem Album Namens >>>Spur im Nebel<<< passen.
Dabei ist folgendes Besonders zu Beachten:
(Albumtitel und mein Künstlername sollte auf die Frontansicht)
Spur im Nebel
Jonas Brehm
(Auf die Rückseite des Album-Covers sollten die Songtitel, Songlänge, Gesamtlänge sowie die weiteren Infos stehen)
1. Intro (Tobi) 1:06
2. Spur im Nebel 3:36
3. Traumfrau (feat. Sven) 3:52
4. Du bist weg 3:22
5. Denke positiv 3:09
6. Familie 2:44
7. Dir Mama 3:48
8. Letzte Sekunde 3:45
9. Liebe gesucht (feat. Sven) 3:15
10. Schöne Zeit 3:18
11. Ich bin da 3:21
12. Karma 2:47
13. Ich geh allein 3:13
14. Nicht gedacht 3:00
15. Sommer 2:51
16. Du bist frei 3:58
17. Schau nicht zurück 3:25
18. Spur im Nebel 3:36
58Min. 6Sek.
Texte & Songwriting by Jonas Brehm I Produziert im Nachtfalke Studio by Sven Ulrich Grabinski I Foto by Helmut K. Fotografie
(weitere Informationen)
>>> Das CD-Cover ist bestimmt für ein vierseitigen Druck und der CD (Voderseite, Rückseite, Innenseite Links, Innenseite Rechts und CD)
Das hochgeladene Fotomaterial sollte im Design mit eingebunden werden. Am besten wäre das Foto mit meiner Wenigkeit auf der Innenseite Links und das andere vorhandene Foto auf der CD selber zu intigrieren. Natürlich bin ich aber auch Offen für Alles und vertraue auf eure künstlerischen Fähigkeiten.
Viel Spaß :)

```html
<!DOCTYPE html>
<html lang="de">
<head>
<meta charset="utf-8">
<title>Spur im Nebel – CD-Cover</title>
<link rel="stylesheet" href="https://fonts.googleapis.com/css2?family=Source+Sans+3:wght@400;600&family=Noto+Serif:wght@400&display=swap">
<style>
  :root {
    --paper: #ffffff;
    --ink-dark: #231f20;
    --accent-red: #c4161c;
    --text-light: #ffffff;
    --mist-top: #8d96a6;
    --mist-mid: #5b616c;
    --rock-low: #2a2724;
    --guide-grey: #9a9a9a;
  }
  html, body {
    margin: 0;
    padding: 0;
    width: 1200px;
    height: 675px;
    overflow: hidden;
    background: var(--paper);
  }
  .sheet { display: block; width: 1200px; height: 675px; }
  .sans { font-family: "Source Sans 3", "Myriad Pro", sans-serif; }
  .serif { font-family: "Noto Serif", Georgia, serif; }
  .panel-dark { fill: var(--ink-dark); }
  .trim-frame { fill: none; stroke: var(--accent-red); stroke-width: 0.7; }
  .bio-text { fill: var(--text-light); font-size: 7px; }
  .tracklist { fill: var(--accent-red); font-size: 6.6px; }
  .credits { fill: var(--text-light); font-size: 3.4px; }
  .red-rule { stroke: var(--accent-red); stroke-width: 2.2; }
  .artist-name { fill: var(--accent-red); font-size: 9px; }
  .album-title { fill: var(--accent-red); font-size: 14.5px; }
  .spine-title { fill: var(--accent-red); font-size: 7px; }
  .spine-small { fill: var(--accent-red); font-size: 2.6px; }
  .disc-title { fill: var(--accent-red); font-size: 12.5px; }
  .die-line { fill: none; stroke: var(--guide-grey); stroke-width: 0.6; stroke-dasharray: 6 4; }
</style>
</head>
<body>
<svg class="sheet" viewBox="0 0 1200 675" xmlns="http://www.w3.org/2000/svg">
  <defs>
    <linearGradient id="waterfall-rock" x1="0" y1="0" x2="0" y2="1">
      <stop offset="0" stop-color="var(--mist-top)"/>
      <stop offset="0.5" stop-color="var(--mist-mid)"/>
      <stop offset="0.62" stop-color="#7a3a34"/>
      <stop offset="0.75" stop-color="var(--rock-low)"/>
      <stop offset="1" stop-color="#1c1a18"/>
    </linearGradient>
    <linearGradient id="portrait-rock" x1="0" y1="0" x2="0" y2="1">
      <stop offset="0" stop-color="#2b2b2d"/>
      <stop offset="0.45" stop-color="#6e6c6a"/>
      <stop offset="0.8" stop-color="#8b8784"/>
      <stop offset="1" stop-color="#3a3b44"/>
    </linearGradient>
    <clipPath id="disc-clip"><circle cx="871" cy="456" r="99"/></clipPath>
  </defs>

  <!-- Inner spread, version A -->
  <g class="inner-spread">
    <rect class="panel-dark" x="80" y="93" width="255" height="233"/>
    <rect x="106" y="93" width="229" height="233" fill="url(#waterfall-rock)" role="img" aria-label="Foto: roter Herzstein auf nassem Felsen vor einem Wasserfall"/>
    <rect class="panel-dark" x="343" y="93" width="255" height="233"/>
    <rect x="343" y="93" width="230" height="233" fill="url(#waterfall-rock)" role="img" aria-label="Foto: roter Herzstein auf nassem Felsen vor einem Wasserfall"/>
    <rect class="trim-frame" x="92.5" y="103.8" width="493" height="208.7"/>
    <rect x="335" y="90" width="8" height="240" fill="var(--paper)"/>
    <text class="sans bio-text" x="122.5" y="126">
      <tspan x="122.5">Liebe soviel Du kannst!</tspan>
      <tspan x="122.5" dy="18">Ich, „Jonas Brehm“ (bürgerlich: Jonas Brenner) wurde 1993</tspan>
      <tspan x="122.5" dy="9">in Freiberg geboren und schrieb meine ersten Texte</tspan>
      <tspan x="122.5" dy="9">und eigene Songs im Alter von ca. 14 Jahren. Mein</tspan>
      <tspan x="122.5" dy="9">Musikstil zeichnet sich durch melodischen Rap aus.</tspan>
      <tspan x="122.5" dy="9">Eine Kombination zwischen Gesang und Rap. Ich</tspan>
      <tspan x="122.5" dy="9">möchte die Menschen mit meiner gefühlvollen Art</tspan>
      <tspan x="122.5" dy="9">inspirieren und sie zur Liebe einladen. Musik war für</tspan>
      <tspan x="122.5" dy="9">mich schon immer die größte Bereicherung in</tspan>
      <tspan x="122.5" dy="9">meinem Leben und genau das möchte ich</tspan>
      <tspan x="122.5" dy="9">weitergeben.</tspan>
      <tspan x="122.5" dy="9">Mein Leitgedanke: Liebe soviel Du kannst!</tspan>
    </text>
  </g>

  <!-- Inner spread, version B -->
  <g class="inner-spread">
    <rect class="panel-dark" x="636" y="93" width="255" height="233"/>
    <rect x="662" y="93" width="229" height="233" fill="url(#waterfall-rock)" role="img" aria-label="Foto: roter Herzstein auf nassem Felsen vor einem Wasserfall"/>
    <rect class="panel-dark" x="899" y="93" width="255" height="233"/>
    <rect x="899" y="93" width="230" height="233" fill="url(#waterfall-rock)" role="img" aria-label="Foto: roter Herzstein auf nassem Felsen vor einem Wasserfall"/>
    <rect class="trim-frame" x="648" y="103.8" width="494.5" height="208.7"/>
    <rect x="891" y="90" width="8" height="240" fill="var(--paper)"/>
    <text class="sans bio-text" x="953" y="128.5">
      <tspan x="953">Liebe soviel Du kannst!</tspan>
      <tspan x="953" dy="18">Ich, „Jonas Brehm“ (bürgerlich: Jonas Brenner) wurde 1993</tspan>
      <tspan x="953" dy="9">in Freiberg geboren und schrieb meine ersten Texte</tspan>
      <tspan x="953" dy="9">und eigene Songs im Alter von ca. 14 Jahren. Mein</tspan>
      <tspan x="953" dy="9">Musikstil zeichnet sich durch melodischen Rap aus.</tspan>
      <tspan x="953" dy="9">Eine Kombination zwischen Gesang und Rap. Ich</tspan>
      <tspan x="953" dy="9">möchte die Menschen mit meiner gefühlvollen Art</tspan>
      <tspan x="953" dy="9">inspirieren und sie zur Liebe einladen. Musik war für</tspan>
      <tspan x="953" dy="9">mich schon immer die größte Bereicherung in</tspan>
      <tspan x="953" dy="9">meinem Leben und genau das möchte ich</tspan>
      <tspan x="953" dy="9">weitergeben.</tspan>
      <tspan x="953" dy="9">Mein Leitgedanke: Liebe soviel Du kannst!</tspan>
    </text>
  </g>

  <!-- Outer cover: back, spine, front -->
  <g class="outer-cover" transform="translate(80 334)">
    <rect class="panel-dark" x="0" y="0" width="518" height="238"/>
    <line class="red-rule" x1="20.6" y1="0" x2="20.6" y2="152"/>
    <line class="red-rule" x1="31.3" y1="21" x2="31.3" y2="173.5"/>
    <line class="red-rule" x1="232" y1="170" x2="232" y2="238"/>

    <text class="sans tracklist" text-anchor="middle" x="125" y="26.5">
      <tspan x="125">1. Intro (Tobi) 1:06</tspan>
      <tspan x="125" dy="9">2. Spur im Nebel 3:36</tspan>
      <tspan x="125" dy="9">3. Traumfrau (feat. Sven) 3:52</tspan>
      <tspan x="125" dy="9">4. Du bist weg 3:22</tspan>
      <tspan x="125" dy="9">5. Denke positiv 3:09</tspan>
      <tspan x="125" dy="9">6. Familie 2:44</tspan>
      <tspan x="125" dy="9">7. Dir Mama 3:48</tspan>
      <tspan x="125" dy="9">8. Letzte Sekunde 3:45</tspan>
      <tspan x="125" dy="9">9. Liebe gesucht (feat. Sven) 3:15</tspan>
      <tspan x="125" dy="9">10. Schöne Zeit 3:18</tspan>
      <tspan x="125" dy="9">11. Ich bin da 3:21</tspan>
      <tspan x="125" dy="9">12. Karma 2:47</tspan>
      <tspan x="125" dy="9">13. Ich geh allein 3:13</tspan>
      <tspan x="125" dy="9">14. Nicht gedacht 3:00</tspan>
      <tspan x="125" dy="9">15. Sommer 2:51</tspan>
      <tspan x="125" dy="9">16. Du bist frei 3:58</tspan>
      <tspan x="125" dy="9">17. Schau nicht zurück 3:25</tspan>
      <tspan x="125" dy="9">18. Spur im Nebel 3:36</tspan>
      <tspan x="125" dy="18">58Min. 6Sek.</tspan>
    </text>
    <text class="sans credits" text-anchor="middle" x="125" y="211">
      <tspan x="125">Texte &amp; Songwriting by Jonas Brehm</tspan>
      <tspan x="125" dy="4.5">Produziert im Nachtfalke Studio by Sven Ulrich Grabinski</tspan>
      <tspan x="125" dy="4.5">Foto by Helmut K. Fotografie</tspan>
    </text>

    <text class="serif spine-title" transform="translate(262 62) rotate(-90)">Spur im Nebel</text>
    <text class="sans spine-small" transform="translate(261.5 228) rotate(-90)">Jonas Brehm</text>

    <path d="M265 0 L412 0 Q455 90 362 238 L265 238 Z" fill="url(#portrait-rock)" role="img" aria-label="Foto: Künstler kniet vor dunklen Felsen und hält ein rotes Herz"/>
    <path d="M412 0 L421 0 Q475 95 371 238 L362 238 Q455 90 412 0 Z" fill="var(--accent-red)"/>
    <rect class="trim-frame" x="282.5" y="8.5" width="219.5" height="220"/>
    <text class="sans artist-name" x="431" y="196">Jonas Brehm</text>
    <text class="serif album-title" x="395" y="216.5">Spur im Nebel</text>
  </g>

  <!-- Disc label -->
  <g class="disc-label">
    <rect class="die-line" x="752.5" y="337.5" width="236.5" height="236.5"/>
    <circle cx="871" cy="456" r="99" fill="var(--ink-dark)"/>
    <rect x="770" y="355" width="154" height="202" clip-path="url(#disc-clip)" fill="url(#portrait-rock)" role="img" aria-label="Foto: Künstler kniet vor dunklen Felsen und hält ein rotes Herz"/>
    <line x1="924.5" y1="374" x2="924.5" y2="539" stroke="var(--accent-red)" stroke-width="1.4"/>
    <text class="serif disc-title" text-anchor="middle" transform="translate(945 453) rotate(-90)">Spur im Nebel</text>
    <circle cx="871" cy="456" r="14" fill="var(--paper)" stroke="var(--ink-dark)" stroke-width="0.6"/>
  </g>
</svg>
</body>
</html>
```